Health and wellnes company needs business cards

We are a Health and wellness business just relocated to Spain. Here nobody knows our business so we would like to put some of our services on the card. Clean design with logo.

Contact Information for Business Card

Brightmeadow
Paula & Oskar Dunbeck
Calle del Almendro 57
Villamar de la Costa
Mobile: 0046 731 402687
info@brightmeadow.example

Font styles to use
Serif

Colors
85cae6
85acd3
b768aa

Requirements
Must have
• these Services somewhere on the card
• - Private or group yoga
• - Reconnective healing
• - Kitesurfing lessons
• - Massage
• LOgo somewhere
Nice to have
• Colours that go with the logo please

```html
<!DOCTYPE html>
<html lang="en">
<head>
<meta charset="utf-8">
<title>Brightmeadow – Business Cards</title>
<link href="https://fonts.googleapis.com/css2?family=Cinzel:wght@400;500&family=Montserrat:wght@400;500&display=swap" rel="stylesheet">
<style>
  :root {
    --bg: #2b2b2d;
    --navy: #1c3a6a;
    --navy-text: #1f3a6e;
    --teal: #6cc4c8;
    --teal-faint: #e6f4f5;
    --grey-text: #6b6f76;
    --white: #ffffff;
    --emboss: #2a4f8c;
  }
  * { box-sizing: border-box; margin: 0; padding: 0; }
  html, body { width: 1200px; height: 960px; overflow: hidden; }
  body {
    background: var(--bg);
    position: relative;
    font-family: "Montserrat", sans-serif;
  }
  .card {
    position: absolute;
    left: 280px;
    width: 640px;
    height: 366px;
    overflow: hidden;
    box-shadow: 0 10px 30px rgba(0,0,0,.45);
  }
  /* Front */
  .card--front { top: 76px; background: var(--navy); }
  .front-brand {
    position: absolute;
    left: 0; right: 0; top: 90px;
    display: flex; flex-direction: column; align-items: center; gap: 18px;
  }
  .front-brand .mark-circle {
    width: 78px; height: 78px; border-radius: 50%;
    border: 4px solid var(--emboss);
  }
  .front-brand .brand-name {
    font-family: "Cinzel", serif;
    font-size: 42px;
    letter-spacing: 1px;
    color: var(--emboss);
  }
  .services {
    position: absolute;
    left: 0; right: 0; bottom: 44px;
    text-align: center;
    color: var(--white);
    font-size: 14.5px;
    letter-spacing: .3px;
  }
  .services .dot { margin: 0 6px; }

  /* Back */
  .card--back { top: 518px; background: var(--white); }
  .decor-circle {
    position: absolute;
    right: -70px; top: -40px;
    width: 360px; height: 360px; border-radius: 50%;
    border: 22px solid var(--teal-faint);
  }
  .back-brand {
    position: absolute; left: 40px; top: 70px;
    display: flex; flex-direction: column; align-items: flex-start; gap: 12px;
  }
  .back-brand .mark-circle {
    width: 72px; height: 72px; border-radius: 50%;
    border: 6px solid var(--teal);
    margin-left: 26px;
  }
  .back-brand .brand-name {
    font-family: "Cinzel", serif;
    font-size: 34px;
    color: var(--navy-text);
  }
  .owners {
    position: absolute; right: 40px; top: 200px;
    font-family: "Cinzel", serif;
    font-size: 17px;
    color: var(--teal);
  }
  .owners .lead { color: var(--navy-text); }
  .contact {
    position: absolute; left: 64px; top: 232px;
    font-size: 14px; line-height: 1.35;
    color: var(--grey-text);
  }
  .contact .address { margin-bottom: 8px; }
  .contact-line { display: flex; align-items: center; gap: 8px; }
  .contact-line svg { width: 12px; height: 12px; flex: none; }
</style>
</head>
<body>

<section class="card card--front">
  <div class="front-brand">
    <span class="mark-circle"></span>
    <span class="brand-name">BRIGHTMEADOW</span>
  </div>
  <p class="services">
    Private or group yoga<span class="dot">•</span>Reconnective healing<span class="dot">•</span>Kitesurfing lessons<span class="dot">•</span>Massage
  </p>
</section>

<section class="card card--back">
  <span class="decor-circle"></span>
  <div class="back-brand">
    <span class="mark-circle"></span>
    <span class="brand-name">BRIGHTMEADOW</span>
  </div>
  <p class="owners"><span class="lead">PAULA &amp;</span> OSKAR DUNBECK</p>
  <div class="contact">
    <p class="address">Calle del Almendro 57<br>Villamar de la Costa</p>
    <p class="contact-line">
      <svg viewBox="0 0 12 12"><rect x="3" y="0.5" width="6" height="11" rx="1" fill="none" stroke="#1f3a6e" stroke-width="1.3"/><circle cx="6" cy="9.5" r=".7" fill="#1f3a6e"/></svg>
      0046 731 402687
    </p>
    <p class="contact-line">
      <svg viewBox="0 0 12 12"><rect x="0.5" y="2.5" width="11" height="7" fill="#1f3a6e"/><path d="M0.5 2.5 L6 6.5 L11.5 2.5" fill="none" stroke="#fff" stroke-width="1"/></svg>
      info@brightmeadow.example
    </p>
    <p class="contact-line">
      <svg viewBox="0 0 12 12"><circle cx="6" cy="6" r="5.5" fill="#1f3a6e"/><path d="M0.5 6 H11.5 M6 0.5 C3 3 3 9 6 11.5 M6 0.5 C9 3 9 9 6 11.5" fill="none" stroke="#fff" stroke-width=".8"/></svg>
      www.brightmeadow.example
    </p>
  </div>
</section>

</body>
</html>
```